Kestrel Motion LLC Sports Therapy and Soft Tissue Injury solutions

We are a company that specializes in Sports Therapy, Physical therapy, muscular rehab, nutrition plans, and personal training. Kestrel Motion travels around the country and world treating athletes and people in the workforce that have Soft Tissue injuries. We are legally partnered with VMR(Vantor Muscle Recovery/vantorrecovery.example) in treating endurance athletes ex. SteelRidge triathalon. We educate our patients on how to sustain a healthy lifestyle.We need a web design that has a Home page summarizing our services, a Physical therapy page, a Personal training and nutrition page. Our ultimate goal is to build relationships with fitness centers, training facilities, and companies that are implementing preventative health measures for their employees. We want to incorporate the VMR logo and Steelridge logo attached in the website but, we want to use our own name (Kestrel Motion LLC) as the main draw. We will provide literature for the website.

Target Market(s)

Grindlane training gyms, Fitness centers, Dance studios, Companies looking for Corporate Wellness programs

Industry/Entity Type

Health And Wellness

Number of Pages Required

4 page

Font styles to use
Sans Serif

Requirements
Must have
• Stock Photos of Athletes training. Examples of Endurance Athletes and Cross training. A mesh of as many sports and training methods as possible. We are a new company and don't have many photos. Easy accessibility to change and add text as the company grows. Vantor Muscle recovery logo incorporated in the back ground of the website. Always visible but does not take over the web page
Nice to have
• Sleek and cool, and masculine design. We want the website to stand out without focusing on one individual. We want to use the website to brand the company (Kestrel Motion LLC) with easy access to social media platforms

```html
<!DOCTYPE html>
<html lang="en">
<head>
<meta charset="utf-8">
<title>Kestrel Motion Health And Wellness</title>
<link href="https://fonts.googleapis.com/css2?family=Lato:ital,wght@0,400;0,700;0,900;1,400;1,700&display=swap" rel="stylesheet">
<style>
:root{
  --green:#6aaa2e;
  --blue:#1e6fb8;
  --ink:#222;
  --text:#444;
  --muted:#666;
  --footer:#1b1b1b;
  --footer-text:#e6e6e6;
  --band:#ebebeb;
  --white:#fff;
}
*{margin:0;padding:0;box-sizing:border-box}
html,body{width:1200px;height:2575px;overflow:hidden}
body{font-family:'Lato',sans-serif;color:var(--text);background:var(--white);position:relative}
.abs{position:absolute}

/* header */
.topline{left:0;top:0;width:1200px;height:5px;background:#555}
.header{left:0;top:5px;width:1200px;height:108px;background:linear-gradient(#fff,#f1f1f1)}
.brand{left:100px;top:22px;display:flex;align-items:center;gap:12px}
.brand-dot{width:52px;height:52px;border-radius:50%;background:var(--green)}
.brand-name{font-size:32px;font-weight:700;color:var(--green);line-height:1}
.brand-sub{font-size:16px;font-weight:700;color:var(--green);letter-spacing:1.5px;margin-top:4px}
.phone{left:748px;top:17px;width:200px;height:36px;border-radius:18px;background:#e7e7e7;display:flex;align-items:center}
.phone-icon{width:36px;height:36px;border-radius:50%;background:var(--green);display:flex;align-items:center;justify-content:center}
.phone-num{font-size:17px;font-weight:700;color:var(--ink);margin-left:22px}
.social{top:17px;width:34px;height:34px;border-radius:50%;background:var(--green)}
.nav{top:76px;font-size:13.5px;font-weight:700;color:var(--ink);letter-spacing:.3px}
.nav.active{color:var(--green)}
.nav-bar{left:482px;top:106px;width:44px;height:4px;background:var(--green)}

/* hero */
.hero{left:0;top:113px;width:1200px;height:478px;background:linear-gradient(100deg,#5a4d3f 0%,#8b7660 35%,#b8a58c 55%,#6c5f51 80%,#3f3730 100%)}
.hero-caption{left:0;top:522px;width:1200px;height:69px;background:rgba(20,20,20,.72);color:var(--white);font-size:29px;font-weight:700;display:flex;align-items:center;justify-content:center}
.hero-arrow{top:288px;width:42px;height:42px;background:rgba(30,30,30,.7);display:flex;align-items:center;justify-content:center}

/* section titles */
.title{left:0;width:1200px;text-align:center;font-weight:700;font-size:31px;color:var(--green)}
.title .blue{color:var(--blue)}
.title .small{font-size:23px}
.rule{left:560px;width:80px;height:2px;background:#333}

.about{left:110px;top:710px;width:980px;font-size:14.5px;line-height:24px;text-align:center;color:var(--text)}
.about p+p{margin-top:10px}

/* specialities */
.spec-bg{left:0;top:858px;width:1200px;height:734px;background:linear-gradient(90deg,#c9c5c0 0%,#e8e8e8 30%,#f0f0f0 55%,#cfcbc6 80%,#dcdcdc 100%)}
.spec-veil{left:0;top:858px;width:1200px;height:734px;background:rgba(255,255,255,.55)}
.spec-icon{left:560px;width:76px;height:76px;border-radius:50%;border:4px solid var(--white);box-shadow:0 0 0 1px #ccc;display:flex;align-items:center;justify-content:center}
.spec-icon.green{background:var(--green)}
.spec-icon.blue{background:var(--blue)}
.spec-head{left:652px;font-size:17.5px;font-weight:900;color:var(--ink);letter-spacing:.5px}
.spec-text{left:652px;width:400px;font-size:12.5px;line-height:19px;color:var(--text)}

/* testimonials */
.quote{left:140px;top:1718px;width:920px;text-align:center;font-style:italic;font-size:14px;line-height:26px;color:var(--text)}
.quote b{font-size:26px;font-style:normal;color:var(--ink);vertical-align:-6px}
.author{left:0;top:1806px;width:1200px;text-align:center;font-style:italic;font-weight:700;font-size:15.5px;color:var(--ink)}
.avatar{top:1849px;width:88px;height:88px;border-radius:50%;border:4px solid #bbb;background:linear-gradient(#c9c2bb,#7d746c)}
.avatar.on{border-color:var(--green)}

/* membership */
.member-band{left:0;top:1995px;width:1200px;height:247px;background:var(--band)}
.member-box{left:347px;top:2107px;width:506px;height:103px;background:var(--white)}

/* footer */
.footer{left:0;top:2242px;width:1200px;height:287px;background:var(--footer)}
.f-head{top:2280px;font-size:16px;font-weight:700;color:var(--white)}
.f-rule{top:2309px;width:28px;height:3px;background:var(--green)}
.f-link{left:100px;font-size:13.5px;color:var(--footer-text);display:flex;align-items:center;gap:10px}
.f-link.current{font-weight:700;color:var(--white)}
.field{left:347px;width:213px;height:31px;border:1px solid #ddd;border-radius:3px;font-size:11.5px;font-weight:700;color:var(--white);padding:8px 10px}
.submit{left:347px;top:2452px;width:213px;height:34px;background:var(--green);color:var(--white);font-weight:700;font-size:15px;display:flex;align-items:center;justify-content:center;border-radius:2px}
.c-row{left:611px;font-size:12.5px;color:var(--footer-text);display:flex;gap:12px;line-height:16px}
.map{left:884px;top:2332px;width:215px;height:153px;border:3px solid #888;background:linear-gradient(135deg,#bcd9ee 0%,#cfe3c2 45%,#e9e6df 70%,#bfe0a6 100%)}
.bottom{left:0;top:2529px;width:1200px;height:46px;background:var(--blue)}
.copy{left:100px;top:2544px;font-size:13px;color:var(--white)}
.b-social{top:2536px;width:30px;height:30px;border-radius:50%;background:var(--green)}
</style>
</head>
<body>

<div class="abs topline"></div>
<header class="abs header"></header>
<div class="abs brand">
  <div class="brand-dot"></div>
  <div>
    <div class="brand-name">Kestrel Motion</div>
    <div class="brand-sub">Health And Wellness</div>
  </div>
</div>
<div class="abs phone">
  <div class="phone-icon">
    <svg width="16" height="16" viewBox="0 0 24 24"><path fill="#fff" d="M6.6 10.8a15 15 0 0 0 6.6 6.6l2.2-2.2a1 1 0 0 1 1-.25 11.4 11.4 0 0 0 3.6.57 1 1 0 0 1 1 1V20a1 1 0 0 1-1 1A17 17 0 0 1 3 4a1 1 0 0 1 1-1h3.5a1 1 0 0 1 1 1c0 1.25.2 2.45.57 3.57a1 1 0 0 1-.25 1z"/></svg>
  </div>
  <span class="phone-num">(555) 204 - 7731</span>
</div>
<div class="abs social" style="left:975px" role="img" aria-label="Social profile 1"></div>
<div class="abs social" style="left:1020px" role="img" aria-label="Social profile 2"></div>
<div class="abs social" style="left:1065px" role="img" aria-label="Social profile 3"></div>

<nav>
  <span class="abs nav active" style="left:482px">HOME</span>
  <span class="abs nav" style="left:575px">PHYSICAL THERAPY</span>
  <span class="abs nav" style="left:750px">PERSONAL TRAINING &amp; NUTRITIO</span>
  <span class="abs nav" style="left:1016px">CONTACT US</span>
</nav>
<div class="abs nav-bar"></div>

<section>
  <div class="abs hero" role="img" aria-label="Athletes training with kettlebells in a gym while a coach watches"></div>
  <div class="abs hero-arrow" style="left:8px"><svg width="14" height="14" viewBox="0 0 10 10"><path d="M7 1 3 5l4 4" stroke="#fff" stroke-width="2" fill="none"/></svg></div>
  <div class="abs hero-arrow" style="left:1150px"><svg width="14" height="14" viewBox="0 0 10 10"><path d="M3 1l4 4-4 4" stroke="#fff" stroke-width="2" fill="none"/></svg></div>
  <div class="abs hero-caption">We Educate Our Patients On How To Sustain a Healthy Lifestyle !</div>
</section>

<section>
  <h2 class="abs title" style="top:625px">About Kestrel Motion <span class="blue small">Health And Wellness</span></h2>
  <div class="abs rule" style="top:681px"></div>
  <div class="abs about">
    <p>We are a company that specializes in Sports Therapy,&nbsp; Physical therapy, muscular rehab, nutrition plans, and personal training. Kestrel Motion&nbsp; travels around the country and world treating athletes and people in the workforce that have Soft tissue injuries. We educate our patients on how to sustain a healthy lifestyle!</p>
    <p>We build relationships with companies committed to the sustainable health of their employees and patrons. We offer Corporate Health Solutions through VMR®. Contact us today for more information About VMR®.</p>
  </div>
</section>

<section>
  <div class="abs spec-bg" role="img" aria-label="Blurred photo of two athletes shaking hands in a gym"></div>
  <div class="abs spec-veil"></div>
  <h2 class="abs title" style="top:916px">We <span class="blue">Specializes In</span></h2>
  <div class="abs rule" style="top:970px"></div>

  <svg class="abs" style="left:400px;top:1090px" width="180" height="370" viewBox="0 0 180 370">
    <path d="M40 30 A200 200 0 0 1 40 340" fill="none" stroke="var(--blue)" stroke-width="5"/>
    <g stroke="#555" stroke-dasharray="3 3" fill="none" stroke-width="1">
      <path d="M62 65 L158 -25"/>
      <path d="M80 115 L158 80"/>
      <path d="M87 185 L158 185"/>
      <path d="M80 255 L158 290"/>
      <path d="M62 305 L158 395"/>
    </g>
  </svg>

  <div class="abs spec-icon green" style="top:1027px"><svg width="34" height="34" viewBox="0 0 24 24"><circle cx="12" cy="6" r="3" fill="#fff"/><rect x="4" y="13" width="16" height="4" rx="2" fill="#fff"/></svg></div>
  <div class="abs spec-head" style="top:1030px">SPORTS THERAPY</div>
  <div class="abs spec-text" style="top:1056px">Lorem ipsum dolor sit amet, consectetuer adipiscing elit, sed diam nonummy nibh euismod tincidunt ut laoreet dolore</div>

  <div class="abs spec-icon blue" style="top:1131px"><svg width="34" height="34" viewBox="0 0 24 24"><circle cx="12" cy="6" r="3" fill="#fff"/><path d="M7 20v-6a5 5 0 0 1 10 0v6z" fill="#fff"/></svg></div>
  <div class="abs spec-head" style="top:1134px">PHYSICAL THERAPY</div>
  <div class="abs spec-text" style="top:1160px">Lorem ipsum dolor sit amet, consectetuer adipiscing elit, sed diam nonummy nibh euismod tincidunt ut laoreet dolore</div>

  <div class="abs spec-icon blue" style="top:1236px"><svg width="34" height="34" viewBox="0 0 24 24"><circle cx="6" cy="15" r="3" fill="#fff"/><rect x="10" y="13" width="11" height="4" rx="2" fill="#fff"/></svg></div>
  <div class="abs spec-head" style="top:1239px">MUSCULAR REHAB</div>
  <div class="abs spec-text" style="top:1265px">Lorem ipsum dolor sit amet, consectetuer adipiscing elit, sed diam nonummy nibh euismod tincidunt ut laoreet dolore</div>

  <div class="abs spec-icon blue" style="top:1341px"><svg width="30" height="30" viewBox="0 0 24 24"><rect x="5" y="3" width="14" height="18" rx="2" fill="none" stroke="#fff" stroke-width="2"/><path d="M8 9h8M8 13h8M8 17h5" stroke="#fff" stroke-width="2"/></svg></div>
  <div class="abs spec-head" style="top:1344px">NUTRITION PLANS</div>
  <div class="abs spec-text" style="top:1370px">Lorem ipsum dolor sit amet, consectetuer adipiscing elit, sed diam nonummy nibh euismod tincidunt ut laoreet dolore</div>

  <div class="abs spec-icon blue" style="top:1447px"><svg width="34" height="34" viewBox="0 0 24 24"><circle cx="8" cy="7" r="3" fill="#fff"/><circle cx="16" cy="9" r="3" fill="#fff"/><path d="M3 20a5 5 0 0 1 10 0zM11 20a5 5 0 0 1 10 0z" fill="#fff"/></svg></div>
  <div class="abs spec-head" style="top:1450px">PERSONAL TRAINING</div>
  <div class="abs spec-text" style="top:1476px">Lorem ipsum dolor sit amet, consectetuer adipiscing elit, sed diam nonummy nibh euismod tincidunt ut laoreet dolore</div>
</section>

<section>
  <h2 class="abs title" style="top:1627px">Client <span class="blue">Testimonials</span></h2>
  <div class="abs rule" style="top:1681px"></div>
  <p class="abs quote"><b>&ldquo;</b> Lorem ipsum dolor sit amet, consectetur adipiscing elit, sed do eiusmod tempor incididunt ut labore et dolore magna aliqua. Ut enim&nbsp; veniam, quis nostrud exercitation ullamco laboris nisi ut aliquip ex ea commodo consequat. Duis aute irure dolor in reprehenderit in voluptate velit esse cillum dolore eu fugiat nulla pariatur. Excepteur sint occaecat cupidatat non proident, sunt in culpa qui officia . <b>&rdquo;</b></p>
  <div class="abs author">- Sconsectetur adipiscing</div>
  <svg class="abs" style="left:586px;top:1836px" width="20" height="14" viewBox="0 0 20 14"><path d="M0 14 10 0l10 14z" fill="var(--green)"/></svg>
  <div class="abs avatar" style="left:445px" role="img" aria-label="Client portrait"></div>
  <div class="abs avatar on" style="left:552px" role="img" aria-label="Client portrait, selected"></div>
  <div class="abs avatar" style="left:656px" role="img" aria-label="Client portrait"></div>
</section>

<section>
  <div class="abs member-band"></div>
  <h2 class="abs title" style="top:2020px">Our <span class="blue">Membership</span></h2>
  <div class="abs rule" style="top:2075px"></div>
  <div class="abs member-box"></div>
  <div class="abs" style="left:385px;top:2133px;width:175px;height:50px;border-radius:25px;background:#9a9a9a" role="img" aria-label="VMR partner badge"></div>
  <div class="abs" style="left:620px;top:2138px;width:190px;height:42px;background:#8d8d8d" role="img" aria-label="Steelridge partner badge"></div>
</section>

<footer>
  <div class="abs footer"></div>
  <div class="abs f-head" style="left:100px">Quick Links</div>
  <div class="abs f-rule" style="left:100px"></div>
  <div class="abs f-link current" style="top:2331px"><span style="color:var(--green)">›</span> Home</div>
  <div class="abs f-link" style="top:2368px"><span style="color:var(--green)">›</span> Physical Therapy</div>
  <div class="abs f-link" style="top:2404px"><span style="color:var(--green)">›</span> Personal Training &amp; Nutritio</div>
  <div class="abs f-link" style="top:2442px"><span style="color:var(--green)">›</span> Contact Us</div>

  <div class="abs f-head" style="left:345px">Quick Inquiry</div>
  <div class="abs f-rule" style="left:345px"></div>
  <div class="abs field" style="top:2332px">Name</div>
  <div class="abs field" style="top:2371px">Email</div>
  <div class="abs field" style="top:2411px">Message</div>
  <div class="abs submit">Submit</div>

  <div class="abs f-head" style="left:611px">Contact Details</div>
  <div class="abs f-rule" style="left:611px"></div>
  <div class="abs c-row" style="top:2331px">
    <svg width="12" height="16" viewBox="0 0 12 16"><path d="M6 0a6 6 0 0 1 6 6c0 4-6 10-6 10S0 10 0 6a6 6 0 0 1 6-6z" fill="var(--green)"/><circle cx="6" cy="6" r="2" fill="var(--footer)"/></svg>
    <div><b style="color:#fff">Kestrel Motion</b><br>1234- Lorem ipsum dolor sitamet,<br>HARBOR CITY - USA -123456</div>
  </div>
  <div class="abs c-row" style="top:2390px"><svg width="13" height="13" viewBox="0 0 24 24"><path fill="var(--green)" d="M6.6 10.8a15 15 0 0 0 6.6 6.6l2.2-2.2a1 1 0 0 1 1-.25 11.4 11.4 0 0 0 3.6.57 1 1 0 0 1 1 1V20a1 1 0 0 1-1 1A17 17 0 0 1 3 4a1 1 0 0 1 1-1h3.5a1 1 0 0 1 1 1c0 1.25.2 2.45.57 3.57a1 1 0 0 1-.25 1z"/></svg>(555) 204 - 7731</div>
  <div class="abs c-row" style="top:2422px"><svg width="14" height="13" viewBox="0 0 14 13"><rect x="3" y="0" width="8" height="4" fill="var(--green)"/><rect x="0" y="4" width="14" height="6" rx="1" fill="var(--green)"/><rect x="3" y="8" width="8" height="5" fill="var(--green)"/></svg>(555) 204 - 7731</div>
  <div class="abs c-row" style="top:2454px"><svg width="14" height="11" viewBox="0 0 14 11"><rect width="14" height="11" rx="1" fill="var(--green)"/><path d="M0 1l7 5 7-5" stroke="var(--footer)" stroke-width="1.2" fill="none"/></svg>health@kestrelmotion.example</div>

  <div class="abs f-head" style="left:881px">Location Map</div>
  <div class="abs f-rule" style="left:881px"></div>
  <div class="abs map" role="img" aria-label="Street map showing the office location"></div>

  <div class="abs bottom"></div>
  <div class="abs copy">Copyright © 2016 Kestrel Motion. All Rights Reserved.</div>
  <div class="abs b-social" style="left:996px" role="img" aria-label="Social profile 1"></div>
  <div class="abs b-social" style="left:1031px" role="img" aria-label="Social profile 2"></div>
  <div class="abs b-social" style="left:1066px" role="img" aria-label="Social profile 3"></div>
</footer>

</body>
</html>
```